Business IT Services Billboard to attract local small businesses

We are Brivoqua, a premier Managed Service Provider (MSP) specializing in comprehensive IT services and VOIP phone solutions exclusively for businesses. Our goal is to create a dynamic and visually engaging billboard advertisement that not only highlights our cutting-edge IT solutions but also emphasizes our state-of-the-art VOIP phone services. This billboard should communicate our commitment to providing innovative, reliable, and holistic technology solutions.
See the attached supporting documentation.
Target Market(s)
small business
Industry/Entity Type
Information Technology
Colors
Designer to choose colors to be used in the design.
Look and feel
Each slider illustrates characteristics of the customer's brand and the style your logo design should communicate.

```html
<!DOCTYPE html>
<html lang="en">
<head>
<meta charset="UTF-8">
<title>Brivoqua – Billboard</title>
<link href="https://fonts.googleapis.com/css2?family=Montserrat:wght@400;500;800;900&family=Poppins:wght@500;600;700&display=swap" rel="stylesheet">
<style>
  :root{
    --navy:#0b2240;
    --navy-deep:#071a33;
    --brand-blue:#1b7ac6;
    --orange:#e0540f;
    --silver:#a9abae;
    --white:#ffffff;
    --ink:#1c1c1c;
    --page:#f4f4f4;
  }
  *{margin:0;padding:0;box-sizing:border-box}
  html,body{width:1078px;height:1200px;overflow:hidden;background:var(--page)}
  .billboard{
    position:absolute;left:39px;top:465px;width:1000px;height:269px;
    background:var(--navy);overflow:hidden;
    box-shadow:0 10px 30px rgba(0,0,0,.18);
  }
  .hero-visual{
    position:absolute;right:0;top:0;width:340px;height:229px;
    background:
      radial-gradient(circle at 38% 38%, rgba(120,220,255,.55) 0, rgba(40,140,210,.25) 22%, transparent 48%),
      linear-gradient(90deg, var(--navy) 0%, #103a6b 35%, #17508c 70%, #1a4f86 100%);
  }
  .brand{
    position:absolute;left:25px;top:18px;
    font-family:'Montserrat',sans-serif;font-weight:900;font-size:40px;
    letter-spacing:1px;color:var(--brand-blue);line-height:1;
  }
  .lead{
    position:absolute;left:25px;top:63px;
    font-family:'Montserrat',sans-serif;font-weight:400;font-size:22px;
    letter-spacing:6.4px;color:var(--white);line-height:1;
  }
  .headline{
    position:absolute;left:22px;
    font-family:'Montserrat',sans-serif;font-weight:800;line-height:1;
  }
  .headline-orange{top:89px;font-size:58px;color:var(--orange);letter-spacing:-0.5px}
  .headline-silver{top:143px;font-size:55px;color:var(--silver);letter-spacing:0}
  .subline{
    position:absolute;left:25px;top:197px;
    font-family:'Poppins',sans-serif;font-weight:500;font-size:15.5px;
    color:var(--white);line-height:1;
  }
  .footer-bar{position:absolute;left:0;top:229px;width:1000px;height:40px}
  .cta{
    position:absolute;left:25px;top:233px;
    font-family:'Poppins',sans-serif;font-weight:700;font-size:25px;
    color:var(--white);line-height:1.2;
  }
  .web{
    position:absolute;left:536px;top:237px;
    font-family:'Poppins',sans-serif;font-weight:600;font-size:22px;
    letter-spacing:7.6px;color:var(--ink);line-height:1.2;
  }
  .web .domain{color:var(--orange)}
</style>
</head>
<body>
  <section class="billboard">
    <div class="hero-visual" role="img" aria-label="Businessman holding a glowing network of technology icons above his open hand"></div>

    <div class="brand">BRIVOQUA</div>
    <p class="lead">ELEVATE YOUR BUSINESS WITH</p>
    <h1 class="headline headline-orange">NEXT-GEN IT &amp;</h1>
    <h2 class="headline headline-silver">VOIP SERVICES</h2>
    <p class="subline">Innovative IT and VOIP Solutions Tailored for Your Business Success.</p>

    <svg class="footer-bar" viewBox="0 0 1000 40" preserveAspectRatio="none" aria-hidden="true">
      <rect x="0" y="0" width="1000" height="40" fill="#ffffff"/>
      <polygon points="0,0 479,0 514,40 0,40" fill="#1b7ac6"/>
    </svg>
    <p class="cta">Transform Your Tech Today!</p>
    <p class="web">www.<span class="domain">brivoqua</span>.com</p>
  </section>
</body>
</html>
```